We need a business card design for a new company located in Brampton Ontario Canada. Our goal is to promote companies to use our service as an "External Program Management " firm taking their industrial product concepts " from prototype to production." We would like to use blue and yellow as our colors. Our skills include finding suppliers for prototype parts and developing them into supplying not only prototypes but the final production parts as well for our customer base.
Industry/Entity Type
Business
Contact Information for Business Card
Derek Namsby
Sales Manager
KOLVEN Solutions Inc.
14 Pinemarsh Lane
Brampton, Ontario L7P 2K9
Canada
Phone: 905-481-2976
Fax: 905-481-2976
website: www.kolvensolutions-example.com
Email: derek@kolvensolutions-example.com
Look and feel
Each slider illustrates characteristics of the customer's brand and the style your logo design should communicate.

```html
<!DOCTYPE html>
<html lang="en">
<head>
<meta charset="utf-8">
<title>KOLVEN Solutions Inc. – Business Card</title>
<link href="https://fonts.googleapis.com/css2?family=Exo+2:wght@400;600;700&display=swap" rel="stylesheet">
<style>
  :root {
    --backdrop: #8c8d8f;
    --card: #ffffff;
    --brand-blue: #1f2fc4;
    --brand-navy: #1a237e;
    --swoosh-grey: #b5b7bb;
    --text-grey: #4a4a4f;
    --on-band: #ffffff;
  }
  html, body {
    margin: 0;
    width: 1200px;
    height: 772px;
    overflow: hidden;
    background: var(--backdrop);
    font-family: "Exo 2", "Segoe UI", sans-serif;
  }
  .canvas {
    position: relative;
    width: 1200px;
    height: 772px;
  }
  .card {
    position: absolute;
    top: 231px;
    width: 540px;
    height: 309px;
    background: var(--card);
    box-shadow: 0 6px 18px rgba(0,0,0,.25);
    overflow: hidden;
  }
  .card--front { left: 40px; }
  .card--back  { left: 620px; }

  .brand-name {
    color: var(--brand-navy);
    font-weight: 700;
    margin: 0;
    line-height: 1;
  }
  .card--front .brand-name {
    position: absolute;
    left: 0; right: 0;
    top: 100px;
    text-align: center;
  }
  .card--front .brand-name .line-main { display: block; font-size: 72px; letter-spacing: 2px; }
  .card--front .brand-name .line-sub  { display: block; font-size: 34px; margin-top: 6px; }

  .card--back .brand-name {
    position: absolute;
    left: 28px;
    top: 22px;
  }
  .card--back .brand-name .line-main { display: block; font-size: 40px; letter-spacing: 1px; }
  .card--back .brand-name .line-sub  { display: block; font-size: 19px; margin-top: 2px; }

  .address {
    position: absolute;
    left: 30px;
    top: 96px;
    font-size: 11.5px;
    line-height: 1.35;
    color: var(--text-grey);
  }
  .person {
    position: absolute;
    right: 28px;
    top: 100px;
    text-align: right;
  }
  .person-name {
    font-size: 15px;
    font-weight: 600;
    color: var(--brand-blue);
  }
  .person-title {
    font-size: 14px;
    color: var(--text-grey);
  }
  .contact-list {
    position: absolute;
    right: 28px;
    top: 178px;
    margin: 0;
    padding: 0;
    list-style: none;
    text-align: right;
    font-size: 12px;
    line-height: 1.55;
    color: var(--text-grey);
  }
  .contact-list li { display: flex; justify-content: flex-end; align-items: center; gap: 6px; }
  .contact-icon { width: 10px; height: 10px; fill: var(--brand-blue); }
  .swoosh {
    position: absolute;
    left: 0; top: 0;
    width: 540px;
    height: 309px;
  }
  .website {
    font-family: "Exo 2", "Segoe UI", sans-serif;
    font-size: 11px;
    letter-spacing: .5px;
    fill: var(--on-band);
  }
</style>
</head>
<body>
<main class="canvas">

  <section class="card card--front" aria-label="Card front">
    <h1 class="brand-name">
      <span class="line-main">KOLVEN</span>
      <span class="line-sub">Solutions Inc.</span>
    </h1>
  </section>

  <section class="card card--back" aria-label="Card back">
    <svg class="swoosh" viewBox="0 0 540 309">
      <defs>
        <path id="band-centre" d="M0,192 C105,197 210,236 275,309"/>
      </defs>
      <path d="M0,150 C120,158 250,205 340,309 L312,309 C228,214 112,176 0,170 Z" fill="var(--swoosh-grey)"/>
      <path d="M0,170 C112,176 228,214 312,309 L236,309 C176,252 90,222 0,216 Z" fill="var(--brand-blue)"/>
      <path d="M0,216 C90,222 176,252 236,309 L212,309 C156,264 78,238 0,232 Z" fill="var(--swoosh-grey)"/>
      <text class="website" dominant-baseline="middle">
        <textPath href="#band-centre" startOffset="70">www.kolvensolutions-example.com</textPath>
      </text>
    </svg>

    <h2 class="brand-name">
      <span class="line-main">KOLVEN</span>
      <span class="line-sub">Solutions Inc.</span>
    </h2>

    <address class="address">
      14 Pinemarsh Lane,<br>
      Brampton, Ontario<br>
      L7P 2K9
    </address>

    <div class="person">
      <div class="person-name">Derek Namsby</div>
      <div class="person-title">Consultant</div>
    </div>

    <ul class="contact-list">
      <li>905-481-2976
        <svg class="contact-icon" viewBox="0 0 10 10" aria-hidden="true"><path d="M2,0 L4,2.5 L3,3.8 C3.6,5 5,6.4 6.2,7 L7.5,6 L10,8 L8.5,10 C4,9.5 0.5,6 0,1.5 Z"/></svg>
      </li>
      <li>905-481-2976
        <svg class="contact-icon" viewBox="0 0 10 10" aria-hidden="true"><rect x="0" y="3" width="10" height="6" rx="1"/><rect x="2" y="0" width="6" height="3"/></svg>
      </li>
      <li>derek@kolvensolutions-example.com
        <svg class="contact-icon" viewBox="0 0 10 10" aria-hidden="true"><rect x="0" y="2" width="10" height="7"/><path d="M0,2 L5,6 L10,2" stroke="#fff" fill="none"/></svg>
      </li>
    </ul>
  </section>

</main>
</body>
</html>
```